project - Misto Den

Dear designers, I'm Looking for an appealing new business card design to represent us for our new e-cigarette store: The MistO Den. Knowledgeable and friendly staff we aim for superior customer service with a positive atmosphere. Classic feel with modern touch is what we are aiming for . Lime green font and grey back round is the original color scheme but we are flexible and open to suggestions. I added some doodles to show you where my mind is at. address: 4827 203 St SW Edmonton, AB (inside the grand swap bazaar)web: themistoden.com email: info@themistoden.com phone : 555.214.6093 Thanks and am looking forward to seeing your creative , fresh and innovative designs.
Good luck everybody!
Gordon
Updates
lime green and charcoal grey please. thanks
Industry/Entity Type
Business
Logo Text
The MistO Den
Look and feel
Each slider illustrates characteristics of the customer's brand and the style your logo design should communicate.

```html
<!DOCTYPE html>
<html lang="en">
<head>
<meta charset="utf-8">
<title>The MistO Den — Business Card</title>
<link href="https://fonts.googleapis.com/css2?family=Signika:wght@400&display=swap" rel="stylesheet">
<style>
  :root {
    --page-bg: #ffffff;
    --card-bg: #242b2d;
    --lime: #b2ec1f;
    --rule-grey: #8a8d8e;
    --icon-grey: #9a9d9e;
  }
  html, body {
    margin: 0;
    padding: 0;
    width: 1200px;
    height: 1000px;
    overflow: hidden;
    background: var(--page-bg);
  }
  .canvas {
    position: relative;
    width: 1200px;
    height: 1000px;
  }
  .card {
    position: absolute;
    left: 57px;
    top: 181px;
    width: 1086px;
    height: 637px;
    background: var(--card-bg);
    font-family: "Signika", "Trebuchet MS", sans-serif;
    color: var(--lime);
  }
  .brand {
    position: absolute;
    left: 120px;
    top: 300px;
    width: 200px;
    display: flex;
    flex-direction: column;
    align-items: center;
    gap: 14px;
  }
  .brand-dot {
    width: 44px;
    height: 44px;
    border-radius: 50%;
    background: var(--lime);
  }
  .brand-name {
    font-size: 28px;
    font-weight: 400;
    color: var(--lime);
    white-space: nowrap;
    letter-spacing: 0.5px;
  }
  .rule {
    position: absolute;
    width: 3px;
  }
  .rule--grey {
    left: 577px;
    top: 384px;
    height: 192px;
    background: var(--rule-grey);
  }
  .rule--lime {
    left: 571px;
    top: 396px;
    height: 194px;
    background: var(--lime);
  }
  .contact {
    position: absolute;
    left: 601px;
    top: 394px;
    font-size: 27px;
    line-height: 1;
  }
  .contact-address {
    margin: 0 0 8px 0;
    line-height: 35px;
  }
  .contact-row {
    display: flex;
    align-items: center;
    height: 39px;
  }
  .contact-icon {
    width: 34px;
    height: 30px;
    margin-right: 8px;
    flex: none;
  }
</style>
</head>
<body>
<div class="canvas">
  <section class="card">
    <div class="brand">
      <span class="brand-dot"></span>
      <span class="brand-name">The MistO Den</span>
    </div>

    <span class="rule rule--grey"></span>
    <span class="rule rule--lime"></span>

    <div class="contact">
      <p class="contact-address">4827 203 St SW Edmonton<br>AB (inside the grand swap bazaar)</p>

      <div class="contact-row">
        <svg class="contact-icon" viewBox="0 0 34 30" aria-hidden="true">
          <g fill="none" stroke="var(--icon-grey)" stroke-width="1.4">
            <circle cx="17" cy="15" r="13"/>
            <ellipse cx="17" cy="15" rx="6" ry="13"/>
            <line x1="4" y1="15" x2="30" y2="15"/>
            <line x1="6" y1="8" x2="28" y2="8"/>
            <line x1="6" y1="22" x2="28" y2="22"/>
          </g>
        </svg>
        <span>: themistoden.com</span>
      </div>

      <div class="contact-row">
        <svg class="contact-icon" viewBox="0 0 34 30" aria-hidden="true">
          <g fill="none" stroke="var(--icon-grey)" stroke-width="1.8">
            <rect x="2" y="7" width="30" height="17"/>
            <polyline points="2,7 17,18 32,7"/>
            <line x1="2" y1="24" x2="13" y2="15"/>
            <line x1="32" y1="24" x2="21" y2="15"/>
          </g>
        </svg>
        <span>: info@themistoden.com</span>
      </div>

      <div class="contact-row">
        <svg class="contact-icon" viewBox="0 0 34 30" aria-hidden="true">
          <path fill="var(--icon-grey)" d="M12 3 L16 3 L17 9 L14 11 C14 16 16 20 19 22 L22 20 L25 24 L22 28 C14 27 9 18 9 10 C9 6 10 4 12 3 Z"/>
        </svg>
        <span>: 555.214.6093</span>
      </div>
    </div>
  </section>
</div>
</body>
</html>
```